Redesign company trifold brochure

We are rebranding our company in September and looking for a more professional design for our brochure.

What we do - providing interdisciplinary care for those supporting ill, elderly and special needs pets at home following the human hospice model of care - is very novel and our brochure is key in explaining it and our offerings.

We serve dogs and cats. Most of the animals are quite sick, elderly. I have many personal and stock photos we can use in the brochure. Please - no pictures of puppies and/or kittens.

The hard part is fitting the info and message into a clear and concise format.

It must be appealing both to pet owners and vets (who are our primary source of patients through referrals).

It should covey WARMTH, COMPASSION, PROFESSIONALISM, and EXPERTISE.

Please look at our website www.TrellisAnimalRespite.com for more info

We have until now used maroon and copper for colors - to reflect the "sunset" of the pets life. BUT are now changing to Navy, Teal and White to reflect calm, trust and competence.

We will use the same logo recolored.

Existing brochure and new logo are attached.

PLEASE ask questions!!
Updates

We have a library of stock images you are welcome to use. All have been legally acquired and we have the right to use them. You DO NOT have to use them, just sending along in case you wish to. https://www.filecrate.example/sh/qk4vrm82zd1pyno/KLQ7Ztbn-Rrfx2mh9sWpYJ4Dc?dl=0

Our colors are NAVY, TEAL and WHITE. For your reference, the navy we use is 99/87/44/55 (CMYK) The Teal we use is 76/11/44/0 (CMYK) Thank you!

Designers -- pleaseuse pictures of older pets (no puppies or kittens). Below is a link to stock photos we own that would be appropriate for use in the brochure. https://www.filecrate.example/sh/w274m6t9pxkr5da/KLRn3GsfwlTVBXEPcq_8ZNj5u?dl=0 THANK YOU!

Designers -- I would VERY much like to include a photo of a pet in a wheel chair. I have personal photos as well as (purchased) stock photos for this purpose which can be found at http://lnk.example/TARHC-Pets-in-Wheelchairs Thank you!!

Today is the last day! Many of you have submitted beautiful designs and others are rolling in. I am so appreciative of your time and energy!! Please do not let the deadline pass without YOUR very BEST entry being submitted!! Thank you! - Miriam & All of us at Trellis Animal Respite & Home Care

Target Market(s)

Pet Owners and Veterinarians

Industry/Entity Type

Pet Care

Font styles to use
Serif

Colors
0455a3
33b8a4
ffffff

Requirements
Must have
• Our logo and information about our services. Pictures of pets. Our contact info. PLEASE NOTE: this is a 2 sided brochure. Please submit both inside and outside.
Should not have
• puppies, kittens - anything off message

```html
<!DOCTYPE html>
<html lang="en">
<head>
<meta charset="utf-8">
<title>Trellis Animal Respite &amp; Home Care – Brochure Inside</title>
<link rel="stylesheet" href="https://fonts.googleapis.com/css2?family=Montserrat:wght@600;700&family=PT+Serif:ital,wght@0,400;0,700;1,400;1,700&display=swap">
<style>
  :root {
    --navy: #0c1f48;
    --teal: #3aaa9b;
    --teal-light: #4dbcad;
    --teal-dark: #2e8f83;
    --white: #ffffff;
    --paper: #f7f8f8;
    --ink: #2f3338;
    --backdrop: #e4e5e6;
  }
  * { box-sizing: border-box; margin: 0; padding: 0; }
  html, body { width: 1200px; height: 800px; overflow: hidden; }
  body {
    background: var(--backdrop);
    font-family: "PT Serif", Georgia, serif;
    color: var(--ink);
  }
  .brochure {
    position: absolute; left: 60px; top: 50px;
    width: 1080px; height: 700px;
    background: var(--paper);
    box-shadow: 0 10px 30px rgba(0,0,0,.18);
    overflow: hidden;
  }
  .panel { position: absolute; top: 0; width: 360px; height: 700px; }
  .panel--left { left: 0; }
  .panel--middle { left: 360px; }
  .panel--right { left: 720px; background: var(--white); border-right: 12px solid var(--teal); border-bottom: 12px solid var(--teal); }

  .section-title {
    font-family: "Montserrat", Arial, sans-serif;
    font-weight: 700; text-transform: uppercase;
    color: var(--teal-light); letter-spacing: .5px;
    text-align: center; line-height: 1.15;
  }
  .title-band { background: var(--navy); }

  /* Left panel */
  .palliative-header { position: absolute; top: 40px; left: 0; width: 300px; height: 78px; padding-top: 14px; font-size: 19px; }
  .palliative-intro { position: absolute; top: 132px; left: 28px; width: 290px; font-size: 12px; line-height: 1.35; }
  .palliative-intro p + p { margin-top: 8px; }
  .palliative-intro em { font-weight: 700; }

  .hero-photo {
    position: absolute; left: 0; top: 0; width: 720px; height: 330px;
    background: linear-gradient(135deg, #c9cdd4 0%, #8a7a68 40%, #4a3a2c 65%, #b8bcc4 100%);
    clip-path: polygon(0 235px, 360px 235px, 360px 0, 720px 0, 720px 330px, 0 330px);
  }
  .shared-care { position: absolute; left: 0; top: 330px; width: 360px; height: 260px; background: var(--teal); padding: 24px 28px 0 34px; color: var(--white); }
  .shared-care h3 { font-style: italic; font-weight: 700; font-size: 14.5px; color: var(--navy); margin-bottom: 10px; }
  .shared-care ul { list-style: none; font-size: 12px; line-height: 1.35; }
  .shared-care li { position: relative; padding-left: 14px; margin-bottom: 12px; }
  .shared-care li::before { content: "•"; position: absolute; left: 0; }
  .care-photo { position: absolute; left: 0; top: 590px; width: 360px; height: 110px; background: linear-gradient(90deg, #a9c9dd 0%, #e8e4dc 45%, #d9c9a4 70%, #eef0f2 100%); }

  /* Middle panel */
  .team { position: absolute; left: 0; top: 330px; width: 360px; height: 370px; background: var(--teal); }
  .team-header { position: absolute; top: 16px; left: 40px; width: 300px; height: 46px; padding-top: 12px; font-size: 19px; }
  .team-lead { position: absolute; top: 80px; left: 40px; width: 290px; font-style: italic; font-weight: 700; font-size: 13.5px; line-height: 1.3; color: var(--navy); }
  .team-list { position: absolute; top: 124px; left: 40px; width: 290px; list-style: none; font-size: 12px; line-height: 1.4; color: var(--white); }
  .team-list li { position: relative; padding-left: 14px; }
  .team-list li::before { content: "•"; position: absolute; left: 0; }
  .brand-band { position: absolute; left: 30px; top: 268px; width: 310px; height: 76px; display: flex; align-items: center; justify-content: center; gap: 12px; }
  .brand-mark { width: 18px; height: 18px; border-radius: 50%; background: var(--teal-light); flex: none; }
  .brand-name { font-family: "PT Serif", Georgia, serif; font-size: 16px; line-height: 1.2; color: var(--white); text-align: left; }

  /* Right panel */
  .services-header { color: var(--teal); font-size: 20px; margin: 26px 0 12px; }
  .services-body { padding: 0 22px 0 30px; font-size: 11.5px; line-height: 1.3; }
  .services-body p { margin-bottom: 7px; }
  .services-body .availability { font-style: italic; font-weight: 700; color: var(--navy); }
  .services-list, .extras-list { list-style: none; }
  .services-list li, .extras-list li { position: relative; padding-left: 13px; }
  .services-list li::before, .extras-list li::before { content: "•"; position: absolute; left: 0; }
  .pet-photo-small { float: right; width: 88px; height: 68px; margin: 70px 0 0 8px; background: linear-gradient(160deg, #eef0f0 0%, #3a3534 55%, #d24a8a 100%); }
  .extras-title { clear: both; font-style: italic; font-weight: 700; color: var(--navy); font-size: 12.5px; margin: 12px 0 6px; }
  .extras { display: flex; gap: 14px; }
  .pet-photo-cat { width: 100px; height: 128px; flex: none; margin-top: 20px; background: linear-gradient(170deg, #cfd3d6 0%, #7d7f84 50%, #c9893e 100%); }
</style>
</head>
<body>
<main class="brochure">
  <div class="hero-photo" role="img" aria-label="Photo of a dog resting beside a tabby cat"></div>

  <section class="panel panel--left">
    <h2 class="section-title title-band palliative-header">Palliative Care<br>&amp; Hospice</h2>
    <div class="palliative-intro">
      <p><em>Palliative Care</em> seeks to relieve suffering and improve quality of life at all stages of illness, injury and disease, whether curable or not.</p>
      <p><em>Hospice</em> is a special kind of Palliative Care focused on those with a life expectancy of less than one year.</p>
    </div>
    <div class="shared-care">
      <h3>Both Palliative Care and Hospice:</h3>
      <ul>
        <li>Focus on living fully</li>
        <li>Recognize and address all suffering – physical, emotional, social and spiritual</li>
        <li>Use a team approach to meet the needs of the animal and his or her family</li>
        <li>Affirm life while viewing death as a natural, normal process</li>
      </ul>
    </div>
    <div class="care-photo" role="img" aria-label="Photo of a veterinary team caring for a Labrador on an exam table"></div>
  </section>

  <section class="panel panel--middle">
    <div class="team">
      <h2 class="section-title title-band team-header">Our Team</h2>
      <p class="team-lead">Lead by Miriam Holloway, C.T. our interdisciplinary team includes:</p>
      <ul class="team-list">
        <li>Certified Thanatologist</li>
        <li>Certified Veterinary Technicians</li>
        <li>Interfaith Spiritual Advisor</li>
        <li>Certified Small Animal Massage Therapist</li>
        <li>Animal Care Specialists</li>
        <li>Hospice Assistants</li>
        <li>Client Care Coordinator</li>
      </ul>
      <div class="brand-band title-band">
        <span class="brand-mark"></span>
        <span class="brand-name">Trellis Animal Respite<br>&amp; Home Care</span>
      </div>
    </div>
  </section>

  <section class="panel panel--right">
    <h2 class="section-title services-header">Our Services</h2>
    <div class="services-body">
      <p>At Trellis Animal Respite &amp; Home Care, our only goal is to support you in providing the very best care for your beloved companion in your own home.</p>
      <p class="availability">We are here for you 24 hours a day, every day of the year.</p>
      <p>We work as a team to address the needs of your entire family. We come with no agenda and no prescribed plan, but rather follow your needs and wishes as they evolve and change over time. Some of the services we offer are:</p>
      <div class="pet-photo-small" role="img" aria-label="Photo of a small senior dog resting on a pink blanket"></div>
      <ul class="services-list">
        <li>Visiting and support</li>
        <li>Administration of medication &amp; fluids</li>
        <li>Overnight and respite care</li>
        <li>Check-ins, exercise and play</li>
        <li>Assistance evaluating pain, quality of life, and end of life choices</li>
        <li>Coordination of care with your vet and other care professionals</li>
        <li>Home cooked meals and treats</li>
        <li>Transportation and errand running</li>
        <li>Equipment and supplies</li>
        <li>Funerals and memorials</li>
        <li>Bereavement support</li>
      </ul>
      <p class="extras-title">Our skilled team members can also provide:</p>
      <div class="extras">
        <div class="pet-photo-cat" role="img" aria-label="Photo of a grey senior cat resting on a blue cushion"></div>
        <ul class="extras-list">
          <li>Massage and Gentle Touch</li>
          <li>Cold LASER Treatments</li>
          <li>Reiki</li>
          <li>Passive Range of Motion (PROM)</li>
          <li>Rehabilitation Support</li>
          <li>Grooming</li>
          <li>Essential Oils</li>
          <li>Calming Flower Essences</li>
          <li>Aroma Therapy</li>
          <li>Music Therapy</li>
          <li>Pet Therapy</li>
        </ul>
      </div>
    </div>
  </section>
</main>
</body>
</html>
```